Business Card Design for Marketing Firm

Looking for business card design for higher end marketing firm. Clean but impressionable/trendy. We are a marketing firm that represents manufacturers in the foodservice equipment and supply industry. Our customers are end users such has hotels, restaurants, country clubs, convention centers and casinos as well as distributors of restaurants supplies and equipment, and manufacturers of foodservice equipment and supplies.
Target Market(s)
Hotels, Restaurants, Supply & Equipment Distributors, Foodservice Manufacturers
Industry/Entity Type
Foodservice/Hospitality
Contact Information for Business Card
Name, Title, Contact Number, Email, Website, Social Media, Address
Requirements
Must have
- Clean & Simple but Serious and Impressionable

```html
<!DOCTYPE html>
<html lang="en">
<head>
<meta charset="utf-8">
<title>Northgate Partners — Business Card</title>
<link href="https://fonts.googleapis.com/css2?family=Open+Sans:wght@400;700&display=swap" rel="stylesheet">
<style>
  :root {
    --navy: #161a72;
    --paper: #f1f1f3;
    --ink: #1d1d24;
    --backdrop: #d6d6d6;
  }
  * { box-sizing: border-box; margin: 0; padding: 0; }
  html, body { width: 1200px; height: 1051px; overflow: hidden; }
  body { background: var(--backdrop); position: relative; font-family: "Open Sans", sans-serif; }

  .card {
    position: absolute; left: 200px; width: 800px; height: 457px;
    background: var(--paper);
    box-shadow: 0 18px 40px rgba(0,0,0,.22);
    overflow: hidden;
  }
  .card--front { top: 38px; border-bottom: 6px solid var(--navy); }
  .card--back  { top: 555px; }

  .wordmark {
    display: flex; align-items: center;
    font-family: "Open Sans", sans-serif; font-weight: 700;
    color: var(--navy); line-height: 1; white-space: nowrap;
  }
  .wordmark__dot { flex: none; border-radius: 50%; background: var(--navy); }
  .brand-rule { height: 2px; background: var(--navy); }

  /* front */
  .front-brand { position: absolute; left: 120px; top: 165px; width: 560px; }
  .front-brand .wordmark { font-size: 40px; gap: 16px; letter-spacing: 1px; }
  .front-brand .wordmark__dot { width: 30px; height: 30px; }
  .front-brand .brand-rule { margin-top: 22px; }
  .social { display: flex; justify-content: center; gap: 8px; margin-top: 22px; }
  .social span { width: 20px; height: 20px; border-radius: 50%; background: var(--navy); }

  /* back */
  .back-shape { position: absolute; inset: 0; }
  .back-brand { position: absolute; left: 46px; top: 190px; width: 320px; }
  .back-brand .wordmark { font-size: 22px; gap: 10px; letter-spacing: .5px; }
  .back-brand .wordmark__dot { width: 18px; height: 18px; }
  .back-brand .brand-rule { margin-top: 14px; }
  .divider { position: absolute; left: 400px; top: 120px; width: 2px; height: 200px; background: var(--navy); }
  .contact { position: absolute; left: 432px; top: 125px; color: var(--ink); }
  .contact__name { font-weight: 700; font-size: 26px; color: var(--navy); letter-spacing: .5px; }
  .contact__title { font-size: 17px; margin-bottom: 14px; }
  .contact__row { display: flex; align-items: center; gap: 8px; font-size: 18px; line-height: 1.5; }
  .contact__row svg { width: 15px; height: 15px; fill: none; stroke: var(--navy); stroke-width: 2; }
  .contact__address { font-size: 18px; line-height: 1.35; margin-top: 10px; }
</style>
</head>
<body>

<section class="card card--front">
  <div class="front-brand">
    <div class="wordmark">
      <span class="wordmark__dot"></span>
      <span class="wordmark__name">NORTHGATE PARTNERS</span>
    </div>
    <div class="brand-rule"></div>
    <div class="social" aria-label="Social media links">
      <span></span><span></span><span></span><span></span><span></span><span></span>
    </div>
  </div>
</section>

<section class="card card--back">
  <svg class="back-shape" viewBox="0 0 800 457" preserveAspectRatio="none" aria-hidden="true">
    <rect width="800" height="457" fill="var(--navy)"/>
    <path d="M0,150 Q40,0 330,0 L800,0 L800,300 Q760,457 470,457 L0,457 Z" fill="var(--paper)"/>
  </svg>
  <div class="back-brand">
    <div class="wordmark">
      <span class="wordmark__dot"></span>
      <span class="wordmark__name">NORTHGATE PARTNERS</span>
    </div>
    <div class="brand-rule"></div>
  </div>
  <div class="divider"></div>
  <div class="contact">
    <p class="contact__name">DANIEL HART</p>
    <p class="contact__title">Managing Director</p>
    <p class="contact__row">
      <svg viewBox="0 0 16 16"><path d="M4 1.5l2.5 3-1.5 1.5c.8 1.8 2.2 3.2 4 4l1.5-1.5 3 2.5-1.5 2.5C7 13 3 9 1.5 4z"/></svg>
      123 456 789
    </p>
    <p class="contact__row">
      <svg viewBox="0 0 16 16"><rect x="1.5" y="3.5" width="13" height="9"/><path d="M1.5 3.5l6.5 5 6.5-5"/></svg>
      info@yourmail.com
    </p>
    <p class="contact__row">
      <svg viewBox="0 0 16 16"><circle cx="8" cy="8" r="6.5"/><path d="M1.5 8h13M8 1.5c-3 3.5-3 9.5 0 13M8 1.5c3 3.5 3 9.5 0 13"/></svg>
      www.yourwebsite.com
    </p>
    <p class="contact__address">Your address, City<br>State, Zip 1234</p>
  </div>
</section>

</body>
</html>
```